Brand new letterhead, business card, email signature etc.

We are a financial company in London, UK. Our website is www.marlowvane.com. We're wanting a complete remodel of the company colours, letter head, business cards, email signatures, etc. Looking to keep the same font for the company name. I have upload a colour palette that we want to work with. We're looking for company letterhead for outgoing letters/ correspondence, letterhead for internal documentation, email signatures, e-letters. etc. Ultimately we will redesign the entire website also. It is important that our clients get a strong, secure, warm, trustworthy, solid feeling and first impression.
Updates

Designs look the same

Target Market(s)

Institutional investors, (ultra) high net worth individuals

Industry/Entity Type

Finance, Invesments banking.

Font styles to use
Other font styles liked:
• Current font is "Champagne & Limousines"

Requirements
Must have
• Must use the colours provided on the PDF uploaded to the portal. The purple = main colour. The red = accent colour.
Nice to have
• Nice to use same font as now for the company name "Corvane". Font is "Champagne & Limousines". Nice to have some reference to the old logo flower, but only subtle.
Should not have
• Do not use the colour red from our website. Use the colours provided on the colour palette PDF that I uploaded in the portal.

```html
<!DOCTYPE html>
<html lang="en">
<head>
<meta charset="utf-8">
<title>Corvane Business Card</title>
<link href="https://fonts.googleapis.com/css2?family=Roboto:wght@300;400;500&display=swap" rel="stylesheet">
<style>
  :root {
    --bg: #1c1c1e;
    --card-white: #f7f7f5;
    --brand-purple: #4b2462;
    --brand-purple-deep: #3a1a4d;
    --brand-purple-light: #633380;
    --accent-red: #c0182e;
    --ink: #2a2a2a;
    --ink-soft: #8a8a8a;
    --white: #ffffff;
  }
  * { margin: 0; padding: 0; box-sizing: border-box; }
  html, body { width: 1200px; height: 963px; overflow: hidden; }
  body {
    background: var(--bg);
    font-family: "Roboto", Arial, sans-serif;
    position: relative;
  }
  .card {
    position: absolute;
    left: 250px;
    width: 700px;
    height: 400px;
    box-shadow: 0 10px 30px rgba(0,0,0,.45);
    overflow: hidden;
  }
  .card--front { top: 60px; background: var(--card-white); }
  .card--back { top: 503px; background: var(--brand-purple); }

  /* Front */
  .name-band {
    position: absolute; left: 0; top: 70px;
    width: 440px; height: 72px;
    background: var(--brand-purple);
    color: var(--white);
    padding: 12px 0 0 60px;
  }
  .name-band .person {
    font-size: 24px; font-weight: 400; letter-spacing: 1px; text-transform: uppercase;
  }
  .name-band .role { font-size: 15px; font-weight: 300; margin-top: 2px; }
  .brand-mark {
    position: absolute; left: 452px; top: 70px;
    width: 72px; height: 72px;
    border: 1.5px solid var(--ink);
  }
  .brand-name {
    position: absolute; left: 470px; top: 152px;
    font-size: 30px; font-weight: 300; letter-spacing: 7px;
    color: var(--ink);
    white-space: nowrap;
  }
  .contact {
    position: absolute; left: 60px; top: 176px;
    list-style: none; font-size: 16px; font-weight: 300; color: var(--ink-soft);
  }
  .contact li { display: flex; align-items: center; gap: 10px; height: 22px; }
  .contact svg { width: 14px; height: 14px; fill: none; stroke: var(--accent-red); stroke-width: 1.6; }
  .divider {
    position: absolute; left: 60px; top: 250px;
    width: 590px; height: 1.5px; background: var(--accent-red);
  }
  .offices {
    position: absolute; left: 330px; top: 268px;
    font-size: 15px; line-height: 19px; color: var(--ink-soft); font-weight: 300;
  }
  .offices .office + .office { margin-top: 10px; }
  .offices .entity { font-weight: 500; color: #7a7a7a; }

  /* Back */
  .petal-art {
    position: absolute; inset: 0;
    background: radial-gradient(ellipse at 62% 55%, var(--brand-purple-light) 0%, var(--brand-purple) 45%, var(--brand-purple-deep) 100%);
  }
  .back-name {
    position: absolute; left: 0; right: 0; top: 160px;
    text-align: center;
    font-size: 64px; font-weight: 300; letter-spacing: 14px;
    color: var(--white);
  }
</style>
</head>
<body>
  <section class="card card--front">
    <div class="name-band">
      <div class="person">Edmund Hale</div>
      <div class="role">Manager</div>
    </div>
    <div class="brand-mark" aria-hidden="true"></div>
    <div class="brand-name">CORVANE</div>

    <ul class="contact">
      <li>
        <svg viewBox="0 0 16 16"><path d="M4 2l3 3-2 2c1 2 2 3 4 4l2-2 3 3-2 2C7 14 2 9 2 4z"/></svg>
        020-7946-0815
      </li>
      <li>
        <svg viewBox="0 0 16 16"><rect x="1.5" y="3.5" width="13" height="9"/><path d="M1.5 3.5l6.5 5 6.5-5"/></svg>
        info@marlowvane.com
      </li>
      <li>
        <svg viewBox="0 0 16 16"><circle cx="8" cy="8" r="6.5"/><path d="M1.5 8h13M8 1.5c3 3 3 10 0 13M8 1.5c-3 3-3 10 0 13"/></svg>
        www.marlowvane.com
      </li>
    </ul>

    <div class="divider"></div>

    <div class="offices">
      <div class="office">
        <div class="entity">Corvane (IOM) Limited</div>
        <div>Tarrant House, Douglas</div>
        <div>Isle of Man, IM98 4QT</div>
      </div>
      <div class="office">
        <div class="entity">Corvane Group Limited</div>
        <div>9th Floor, 14 Wexley Court</div>
        <div>London, EC2M 7LP</div>
      </div>
    </div>
  </section>

  <section class="card card--back">
    <div class="petal-art" role="img" aria-label="Embossed flower petal illustration in tonal purple"></div>
    <div class="back-name">CORVANE</div>
  </section>
</body>
</html>
```